USA Home and Kitchen "Multi-Product" Brand Needs a Stunning Packaging Design.

We need a new packaging design for our Brand: T&M Hearth & Dwelling. We Manufacture, Market, and Sell Home & Kitchen Products (Such as Kitchen Utensils and Home Decor to name a few) Direct to Consumers in the United States via our Website and Vendorly.com. We would like to see designs that are simple, clean, and modern, yet stand out and demand attention. Our Preferred colors of the design should include: Black or Grey as the base color/shade), White or Grey for the text, and some additional color can be used for complementary elements/visuals at your own discretion or creativity. We would like this to be an Interchangeable Design that can be easily modified and implemented across all of our other products (i.e: does not contain too many images or design elements that reference a particular product.

Although this design and the concept as a whole is intended to be used across our entire catalogue of products. Please feel free to base your design on our one of our top selling products as per the following URL: https://www.vendorly-example.com/dp/X93QL7714R?ref=abc_title_dp.

Target Market(s)

Our customers tend come from many areas across the spectrum. But the quintessential T&M target customer (the type of person who tends to be our most receptive and loyal customer) is female and part of the Millennials generation, aged in her 30s, and is either working full-time in a white-collar job or on home duties, of which she would have young children, a spouse, or other family members to look after. She’s part of the conventional family life who represent the core of ‘middle America’. She doesn’t mind to splurge every now and again on shopping for items that she wants and/or needs, whilst some of the time she’ll also go out of her way to ‘search for a bargain’. She tends to spend more time in her home and kitchen than the average individual. We recognize that cooking for herself and family, and providing a well furnished and stylish home is part of who she is.

Industry/Entity Type

Retail

Font styles to use
Serif
Sans Serif

Colors

Designer to choose only greyscale colors for use in the design.

Requirements
Must have
• Interchangeable Design (A "Universal" Packaging Design that can be easily modified and adapted for use with a large catalogue of products under our brand).
Nice to have
• Some visual elements that gives our packaging/brand the ability to stand out and be unique/memorable.
Should not have
• Our design should not have too much text. Nor should it be cluttered or overcrowded with too much information or visual elements. And does not contain too many images or design elements that reference a particular product. We believe simplicity is key, and quality over quantity.

```html
<!DOCTYPE html>
<html lang="en">
<head>
<meta charset="utf-8">
<title>T&amp;M Hearth &amp; Dwelling — Pie Server Carton Dielines</title>
<link href="https://fonts.googleapis.com/css2?family=Oswald:wght@300;400;600&family=Questrial&family=Montserrat:wght@700&display=swap" rel="stylesheet">
<style>
  :root {
    --page: #ffffff;
    --amber: #f5a01a;
    --forest: #0d2410;
    --navy: #0e1e27;
    --mist: #c6c6c6;
    --brush: #bdbdbd;
    --gold: #f7b24a;
    --white: #ffffff;
    --fold: #d42a2a;
  }
  html, body {
    margin: 0;
    width: 907px;
    height: 1200px;
    overflow: hidden;
    background: var(--page);
  }
  .sheet {
    position: relative;
    width: 907px;
    height: 1200px;
  }
  .dieline {
    position: absolute;
    top: 341px;
    width: 440px;
    height: 518px;
  }
  .dieline--amber { left: 14px; }
  .dieline--navy { left: 453px; }
  .brand-name { font-family: "Oswald", sans-serif; font-weight: 600; }
  .product-title { font-family: "Oswald", sans-serif; }
  .body-copy { font-family: "Questrial", sans-serif; }
  .lead-copy { font-family: "Montserrat", sans-serif; font-weight: 700; }
  .badge-label { font-family: "Oswald", sans-serif; font-weight: 400; }
</style>
</head>
<body>
<main class="sheet">

  <!-- Amber and forest carton -->
  <svg class="dieline dieline--amber" viewBox="0 0 785 925" xmlns="http://www.w3.org/2000/svg" aria-label="T&amp;M Hearth &amp; Dwelling pie server carton, amber edition">
    <rect class="panel-base" x="0" y="0" width="785" height="925" fill="var(--amber)"/>
    <polygon class="colour-band" points="0,410 785,150 785,925 0,925" fill="var(--forest)"/>

    <g class="brand-name" fill="var(--forest)" text-anchor="middle">
      <text x="133" y="150" font-size="86">T&amp;M</text>
      <text x="133" y="196" font-size="27" textLength="220" lengthAdjust="spacingAndGlyphs">HEARTH &amp; DWELLING</text>
      <text x="330" y="120" font-size="44">T&amp;M</text>
    </g>

    <g class="product-title" fill="var(--amber)">
      <text transform="translate(228,905) rotate(-90)" font-size="58" font-weight="600" font-style="italic">PIE SERVER</text>
      <text transform="translate(256,905) rotate(-90)" font-size="24" font-weight="300">CUT AND SERVE SPATULA</text>
    </g>

    <g class="badges" fill="none" stroke="var(--amber)" stroke-width="2">
      <circle cx="330" cy="872" r="32"/>
      <circle cx="330" cy="800" r="32"/>
      <circle cx="330" cy="728" r="32"/>
    </g>
    <g class="badge-label" fill="var(--amber)" font-size="11" text-anchor="middle">
      <text transform="translate(327,872) rotate(-90)">STSINLESS</text>
      <text transform="translate(341,872) rotate(-90)">STEEL</text>
      <text transform="translate(327,800) rotate(-90)">SERRATED</text>
      <text transform="translate(341,800) rotate(-90)">EDGE</text>
      <text transform="translate(327,728) rotate(-90)">PERFECT FOR</text>
      <text transform="translate(341,728) rotate(-90)">PIE &amp;CAKE</text>
    </g>

    <g class="body-copy" fill="var(--white)" font-size="14">
      <text transform="translate(490,905) rotate(-90)">Lorem ipsum dolor sit amet, consectetuer adipiscing elit, sed diam nonummy</text>
      <text transform="translate(512,905) rotate(-90)">nibh euismod tincidunt ut laoreet dolore magna aliquam erat volutpat. Ut wisi</text>
      <text transform="translate(534,905) rotate(-90)">enim ad minim veniam, quis nostrud exerci tation ullamcorper suscipit lobortis</text>
      <text transform="translate(556,905) rotate(-90)">nisl ut aliquip ex ea commodo consequat. Duis autem vel eum iriure dolor in</text>
      <text transform="translate(578,905) rotate(-90)">hendrerit in vulputate velit esse molestie consequat, vel illum dolore eu feugiat</text>
      <text transform="translate(600,905) rotate(-90)">nulla facilisis at vero eros et accumsan et iusto odio dignissim qui blandit prae-</text>
      <text transform="translate(622,905) rotate(-90)">sent luptatum zzril delenit augue duis dolore te feugait nulla facilisi.</text>
    </g>

    <g class="lead-copy" fill="var(--white)" font-size="17">
      <text transform="translate(700,905) rotate(-90)">Lorem ipsum dolor sit amet, consectetuer</text>
      <text transform="translate(726,905) rotate(-90)">adipiscing elit, sed diam nonummy nibh euis-</text>
      <text transform="translate(752,905) rotate(-90)">mod tincidunt ut laoreet dolore magna ali-</text>
    </g>

    <g class="fold-lines" stroke="var(--fold)" stroke-width="1.5" fill="none">
      <rect x="0.75" y="0.75" width="783.5" height="923.5"/>
      <line x1="267" y1="0" x2="267" y2="925"/>
      <line x1="392" y1="0" x2="392" y2="925"/>
      <line x1="660" y1="0" x2="660" y2="925"/>
    </g>
  </svg>

  <!-- Navy and grey carton -->
  <svg class="dieline dieline--navy" viewBox="0 0 785 925" xmlns="http://www.w3.org/2000/svg" aria-label="T&amp;M Hearth &amp; Dwelling pie server carton, navy edition">
    <rect class="panel-base" x="0" y="0" width="785" height="925" fill="var(--navy)"/>
    <polygon class="colour-band" points="0,0 392,0 392,180 0,70" fill="var(--mist)"/>

    <text class="brand-name" x="22" y="46" font-size="24" font-weight="400" fill="var(--navy)" textLength="225" lengthAdjust="spacingAndGlyphs">T&amp;M HEARTH &amp; DWELLING</text>
    <text class="brand-name" x="330" y="115" font-size="44" fill="var(--gold)" text-anchor="middle">T&amp;M</text>

    <polygon class="brush-area" role="img" aria-label="Grey dry-brush stroke texture behind the brand name" points="60,300 220,270 255,470 190,560 70,520 40,400" fill="var(--brush)"/>
    <text class="brand-name" x="148" y="445" font-size="84" fill="var(--gold)" text-anchor="middle">T&amp;M</text>

    <g class="product-title" fill="var(--gold)" font-weight="300">
      <text transform="translate(228,905) rotate(-90)" font-size="58">PIE SERVER</text>
      <text transform="translate(256,905) rotate(-90)" font-size="24">CUT AND SERVE SPATULA</text>
    </g>

    <g class="badges" fill="none" stroke="var(--gold)" stroke-width="2">
      <circle cx="330" cy="872" r="32"/>
      <circle cx="330" cy="800" r="32"/>
      <circle cx="330" cy="728" r="32"/>
    </g>
    <g class="badge-label" fill="var(--gold)" font-size="11" text-anchor="middle">
      <text transform="translate(327,872) rotate(-90)">STSINLESS</text>
      <text transform="translate(341,872) rotate(-90)">STEEL</text>
      <text transform="translate(327,800) rotate(-90)">SERRATED</text>
      <text transform="translate(341,800) rotate(-90)">EDGE</text>
      <text transform="translate(327,728) rotate(-90)">PERFECT FOR</text>
      <text transform="translate(341,728) rotate(-90)">PIE &amp;CAKE</text>
    </g>

    <g class="body-copy" fill="var(--white)" font-size="13" text-anchor="middle">
      <text transform="translate(432,540) rotate(-90)">Lorem ipsum dolor sit amet, consectetuer adipiscing elit, sed diam nonummy nibh euismod tincidunt ut</text>
      <text transform="translate(452,540) rotate(-90)">laoreet dolore magna aliquam erat volutpat. Ut wisi enim ad minim veniam, quis nostrud exerci tation</text>
      <text transform="translate(472,540) rotate(-90)">ullamcorper suscipit lobortis nisl ut aliquip ex ea commodo consequat. Duis autem vel eum iriure dolor in</text>
      <text transform="translate(492,540) rotate(-90)">hendrerit in vulputate velit esse molestie consequat, vel illum dolore eu feugiat nulla facilisis at vero eros</text>
      <text transform="translate(512,540) rotate(-90)">et accumsan et iusto odio dignissim qui blandit praesent luptatum zzril delenit augue duis dolore te feu-</text>
      <text transform="translate(532,540) rotate(-90)">gait nulla facilisi.</text>
      <text transform="translate(552,540) rotate(-90)">Lorem ipsum dolor sit amet, cons ectetuer adipiscing elit, sed diam nonummy nibh euismod tincidunt ut</text>
      <text transform="translate(572,540) rotate(-90)">laoreet dolore magna aliquam erat volutpat. Ut wisi enim ad minim veniam, quis nostrud exerci tation</text>
      <text transform="translate(592,540) rotate(-90)">ullamcorper suscipit lobortis nisl ut aliquip ex ea commodo consequat.</text>
    </g>

    <g class="body-copy" fill="var(--white)" font-size="16">
      <text transform="translate(705,905) rotate(-90)">Lorem ipsum dolor sit amet, consectetuer adipiscing elit, sed diam nonummy</text>
      <text transform="translate(729,905) rotate(-90)">nibh euismod tincidunt ut laoreet dolore magna aliquam erat volutpat. Ut wisi</text>
      <text transform="translate(753,905) rotate(-90)">enim ad minim veniam, quis nostrud exerci tation ullamcorper suscipit lobor-</text>
    </g>

    <g class="fold-lines" stroke="var(--fold)" stroke-width="1.5" fill="none">
      <rect x="0.75" y="0.75" width="783.5" height="923.5"/>
      <line x1="267" y1="0" x2="267" y2="925"/>
      <line x1="392" y1="0" x2="392" y2="925"/>
      <line x1="660" y1="0" x2="660" y2="925"/>
    </g>
  </svg>

</main>
</body>
</html>
```